Bramblewood Joinery Website

My client Bramblewood Joinery is looking for a redesign for a Word Press Website. Their current site is at www.bramblewoodjoinery.example They are a custom cabinet company, but also create bathroom, living room, bar and entertainment and bedroom cabinets too. They would like a design that emulates the master craftsman work they do yet a contemporary style.

Their current site was designed using Flash elements.

Target Market(s)

Home owners and builders of high end homes

Industry/Entity Type

Entertainment

Font styles to use
Serif
Decorative

Requirements
Must have
• Must show their work and logo using a contemporary style.
Nice to have
• Sliders that showcase their projects.

```html
<!DOCTYPE html>
<html lang="en">
<head>
<meta charset="utf-8">
<title>Bramblewood Joinery</title>
<link rel="stylesheet" href="https://fonts.googleapis.com/css2?family=Raleway:wght@400;500;600&family=Open+Sans:wght@400;600&display=swap">
<style>
:root{
  --green:#2f9e2f;
  --green-dark:#1f7f1f;
  --green-light:#3fb43f;
  --ink:#222222;
  --text:#333333;
  --line:#d8d8d8;
  --footer:#333333;
  --white:#ffffff;
}
*{box-sizing:border-box;margin:0;padding:0}
html,body{width:972px;height:1200px;overflow:hidden;background:var(--white)}
body{position:relative;font-family:"Open Sans",Arial,sans-serif;color:var(--text)}
.abs{position:absolute}

.call{right:110px;top:26px;text-align:right;font-family:"Raleway",sans-serif}
.call-label{color:var(--green);font-size:12px}
.call-number{color:var(--ink);font-size:15px;font-weight:600;display:flex;align-items:center;gap:3px;justify-content:flex-end}

.nav{left:112px;top:68px;width:750px;height:36px;background:linear-gradient(var(--green-light),var(--green))}
.nav a{position:absolute;top:0;line-height:36px;color:var(--white);text-decoration:none;font-family:"Raleway",sans-serif;font-size:11px;font-weight:500;letter-spacing:.2px}

.brand{left:441px;top:32px;width:92px;height:92px;border-radius:50%;background:var(--white);border:3px solid var(--ink);display:flex;align-items:center;justify-content:center;text-align:center}
.brand span{font-family:"Raleway",sans-serif;font-weight:600;font-size:11px;color:var(--green-dark);line-height:1.25}

.hero{left:112px;top:104px;width:750px;height:330px;
  background:
    radial-gradient(ellipse 60px 40px at 104px 18px,rgba(255,250,235,.95),rgba(255,250,235,0)),
    radial-gradient(ellipse 60px 40px at 175px 10px,rgba(255,250,235,.95),rgba(255,250,235,0)),
    radial-gradient(ellipse 260px 70px at 200px 300px,#f2f0ec 0%,#e4e1dc 55%,rgba(228,225,220,0) 100%),
    radial-gradient(ellipse 90px 110px at 610px 260px,#eeeeec,rgba(238,238,236,0)),
    linear-gradient(180deg,rgba(0,0,0,0) 62%,#8e8a84 68%,#e4e3df 72%,#d9d8d4 100%),
    linear-gradient(90deg,#cfc9bf 0%,#e8e5e0 18%,#d8d2c8 40%,#b7ab9f 55%,#e6e4e0 72%,#dddcd8 92%,#7d7f82 100%)}
.caption{left:137px;top:211px;width:293px;height:131px;background:rgba(40,40,40,.82);padding:18px 24px;color:var(--white)}
.caption .kicker{font-family:"Raleway",sans-serif;font-size:19px;line-height:1.2}
.caption h1{font-family:"Raleway",sans-serif;font-weight:400;font-size:29px;line-height:1.1;margin-top:1px;white-space:nowrap}
.caption p{font-size:8.8px;line-height:1.6;color:#ddd;margin-top:8px;padding-left:4px}
.dots{left:466px;top:412px;display:flex;gap:3px}
.dots i{width:8px;height:8px;border-radius:50%;background:var(--white)}
.dots i.on{background:var(--green)}

.services{left:0;top:434px;width:972px;height:172px;background:linear-gradient(#ffffff,#eeeeee)}
.service{top:30px;width:130px;margin-left:-65px;text-align:center}
.service .ring{width:63px;height:63px;margin:0 auto;border-radius:50%;border:2px solid var(--line);background:var(--white);display:flex;align-items:center;justify-content:center}
.service h3{font-family:"Raleway",sans-serif;font-weight:500;font-size:13.5px;color:var(--ink);margin-top:10px}
.service p{font-size:9px;color:var(--text);margin-top:3px}

.about{left:116px;top:654px;width:450px}
.about h2{font-family:"Raleway",sans-serif;font-weight:400;font-size:21px;color:var(--ink)}
.about p{font-size:8.6px;line-height:1.63;color:var(--text);margin-top:7px}
.video{left:590px;top:649px;width:264px;height:161px;border:1px solid var(--line);padding:5px;background:var(--white);box-shadow:0 0 3px rgba(0,0,0,.12)}
.video .shot{width:100%;height:100%;
  background:
    linear-gradient(180deg,rgba(0,0,0,0) 72%,#3a2a22 82%,#2a1d18 100%),
    linear-gradient(90deg,#1e1e1e 0%,#3a3a3a 25%,#5e5e5e 40%,#c9c7c2 55%,#dcdad5 75%,#b7b4ae 100%);
  display:flex;align-items:center;justify-content:center}
.play{width:32px;height:32px;border-radius:50%;background:var(--white);display:flex;align-items:center;justify-content:center}

.card{top:854px;width:237px;text-align:center}
.card .photo{height:100px}
.card h3{font-family:"Raleway",sans-serif;font-weight:500;font-size:17px;color:var(--green);margin-top:11px}
.card p{font-size:8.6px;line-height:1.65;color:#444;margin-top:3px}
.btn{display:inline-block;margin-top:8px;width:80px;height:23px;line-height:23px;background:linear-gradient(var(--green-light),var(--green-dark));color:var(--white);font-size:9px;font-weight:600;text-decoration:none;border-radius:2px}

.footer{left:0;top:1106px;width:972px;height:94px;background:var(--footer)}
.footer-nav{left:112px;top:27px;font-family:"Raleway",sans-serif;font-size:10px;font-weight:600;color:var(--white)}
.footer-nav a{color:var(--white);text-decoration:none}
.footer-nav span{margin:0 5px}
.legal{left:112px;top:52px;font-size:8.5px;color:#aaa}
.social{left:781px;top:28px;display:flex;gap:5px}
.social a{width:19px;height:19px;background:var(--white);border-radius:4px;display:flex;align-items:center;justify-content:center}
.social a i{width:11px;height:11px;border:2px solid var(--footer);border-radius:2px}
</style>
</head>
<body>

<div class="abs call">
  <div class="call-label">Call Us Now</div>
  <div class="call-number">
    <svg width="12" height="12" viewBox="0 0 24 24"><path fill="#444" d="M6.6 10.8a15.1 15.1 0 006.6 6.6l2.2-2.2c.3-.3.7-.4 1-.2 1.1.4 2.3.6 3.6.6.6 0 1 .4 1 1V20c0 .6-.4 1-1 1C10.6 21 3 13.4 3 4c0-.6.4-1 1-1h3.5c.6 0 1 .4 1 1 0 1.3.2 2.5.6 3.6.1.3 0 .7-.2 1z"/></svg>
    555.014.2290
  </div>
</div>

<nav class="abs nav">
  <a style="left:25px">HOME</a>
  <a style="left:70px">WHO WE ARE</a>
  <a style="left:154px">GET STARTED</a>
  <a style="left:239px">PROFESSIONAL</a>
  <a style="left:441px">PORTFOLIO</a>
  <a style="left:514px">CABINET HARDWARE</a>
  <a style="left:637px">CONTACT US</a>
</nav>

<div class="abs brand"><span>Bramblewood<br>Joinery</span></div>

<div class="abs hero" role="img" aria-label="Bright white kitchen with marble island, range, tiled backsplash and pendant lights"></div>
<div class="abs caption">
  <div class="kicker">Morbi ornare gravida</div>
  <h1>Cabinet &amp; Fixtures</h1>
  <p>Morbi porta libero id ullamcorper nonummy nibh ligula<br>pulvinar metus eget consectetuer augue nisi quis</p>
</div>
<div class="abs dots"><i class="on"></i><i></i><i></i><i></i></div>

<section class="abs services">
  <div class="abs service" style="left:191px">
    <div class="ring"><svg width="38" height="30" viewBox="0 0 38 30" fill="none" stroke="#2f9e2f" stroke-width="2"><rect x="2" y="2" width="34" height="22"/><line x1="2" y1="9" x2="36" y2="9"/><rect x="12" y="14" width="14" height="6"/><line x1="6" y1="24" x2="6" y2="28"/><line x1="32" y1="24" x2="32" y2="28"/></svg></div>
    <h3>KITCHENS</h3><p>Lorem ipsum dolor sit amet</p>
  </div>
  <div class="abs service" style="left:338px">
    <div class="ring"><svg width="40" height="32" viewBox="0 0 40 32" fill="none" stroke="#2f9e2f" stroke-width="2"><rect x="3" y="10" width="34" height="20"/><line x1="20" y1="10" x2="20" y2="30"/><line x1="3" y1="17" x2="20" y2="17"/><circle cx="8" cy="5" r="3"/><path d="M28 10V3h5"/></svg></div>
    <h3>BATHROOM</h3><p>Lorem ipsum dolor sit amet</p>
  </div>
  <div class="abs service" style="left:479px">
    <div class="ring"><svg width="30" height="36" viewBox="0 0 30 36" fill="#2f9e2f"><rect x="2" y="16" width="7" height="18"/><rect x="11" y="8" width="8" height="26"/><rect x="21" y="2" width="7" height="32"/></svg></div>
    <h3>OFFICE</h3><p>Lorem ipsum dolor sit amet</p>
  </div>
  <div class="abs service" style="left:626px">
    <div class="ring"><svg width="36" height="32" viewBox="0 0 36 32" fill="#2f9e2f"><path d="M18 2L2 16h5v14h22V16h5z"/><path d="M13 14l10 10M23 14L13 24" stroke="#fff" stroke-width="2.5"/></svg></div>
    <h3>WORKSHOP</h3><p>Lorem ipsum dolor sit amet</p>
  </div>
  <div class="abs service" style="left:780px">
    <div class="ring"><svg width="34" height="26" viewBox="0 0 34 26" fill="none" stroke="#2f9e2f" stroke-width="2.5"><rect x="2" y="2" width="30" height="22"/><path d="M6 20l8-8 5 5 4-3 6 6z" fill="#2f9e2f" stroke="none"/><circle cx="24" cy="8" r="2.5" fill="#2f9e2f" stroke="none"/></svg></div>
    <h3>PHOTOGALLERY</h3><p>Lorem ipsum dolor sit amet</p>
  </div>
</section>

<section class="abs about">
  <h2>Little About Our Company</h2>
  <p>At Bramblewood Joinery, we've been designing and manufacturing the Midwest's finest custom cabinets and fixtures since 1966. From single cabinets to room remodels to entire home installations, our expert artisans help turn the house you live in to the home you've always dreamed of</p>
  <p>Vivamus porttitor purus nisi eleifend libero a tempus libero lectus feugiat felis Morbi diam mauris viverra in gravida eu mattis in ante Morbi eget arcu Morbi porta libero id ullamcorper nonummy nibh ligula pulvinar metus eget consectetuer augue nisi quis lacus Ut ac mi quis lacus mollis aliquam Curabitur iaculis tempus eros Curabitur vel mi sit amet magna malesuada ultrices Ut nisi erat fermentum vel congue id euismod in elit</p>
</section>
<div class="abs video">
  <div class="shot" role="img" aria-label="Video still of a white kitchen island with built-in oven on a dark wood floor">
    <div class="play"><svg width="12" height="14" viewBox="0 0 12 14"><path d="M1 0l11 7-11 7z" fill="#111"/></svg></div>
  </div>
</div>

<article class="abs card" style="left:112px">
  <div class="photo" role="img" aria-label="Warm-lit kitchen with range hood, white cabinets and dark counters" style="background:linear-gradient(180deg,rgba(0,0,0,0) 60%,#2a211c 72%,#6b5646 100%),linear-gradient(90deg,#3b2f27 0%,#7a6553 20%,#e3dacd 42%,#f1ebe2 55%,#cdbfae 72%,#efe9e0 88%,#8b7a68 100%)"></div>
  <h3>Why Choose Us</h3>
  <p>Aullamcorper nonummy nibh ligula pulvinar metus eget<br>consectetuer augue nisi quis lacus Ut ac mi quis lacus<br>mollis aliquam Curabitur iaculis tempus</p>
  <a class="btn">READ MORE</a>
</article>
<article class="abs card" style="left:367px">
  <div class="photo" role="img" aria-label="White kitchen with steel fridge, range hood and marble island" style="background:linear-gradient(180deg,rgba(0,0,0,0) 66%,#d9d3ca 76%,#5a4a3c 100%),linear-gradient(90deg,#ece8e2 0%,#9a9a9a 12%,#c8c8c6 22%,#f2eee8 40%,#e6dccf 55%,#f4f0ea 75%,#ddd7cf 100%)"></div>
  <h3>Customer Experience</h3>
  <p>Aullamcorper nonummy nibh ligula pulvinar metus eget<br>consectetuer augue nisi quis lacus Ut ac mi quis lacus<br>mollis aliquam Curabitur iaculis tempus</p>
  <a class="btn">READ MORE</a>
</article>
<article class="abs card" style="left:622px">
  <div class="photo" role="img" aria-label="Black painted cabinetry on a dark wood floor" style="background:linear-gradient(180deg,rgba(0,0,0,0) 78%,#4a3a30 100%),linear-gradient(90deg,#8a8580 0%,#1c1c1c 12%,#2e2e2e 35%,#1a1a1a 60%,#3a3432 80%,#6a5e52 100%)"></div>
  <h3>Get Started Now</h3>
  <p>Aullamcorper nonummy nibh ligula pulvinar metus eget<br>consectetuer augue nisi quis lacus Ut ac mi quis lacus<br>mollis aliquam Curabitur iaculis tempus</p>
  <a class="btn">READ MORE</a>
</article>

<footer class="abs footer">
  <div class="abs footer-nav">
    <a>HOME</a><span>|</span><a>WHO WE ARE</a><span>|</span><a>GET STARTED</a><span>|</span><a>PROFESSIONAL</a><span>|</span><a>PORTFOLIO</a><span>|</span><a>CABINET HARDWARE</a><span>|</span><a>CONTACT US</a>
  </div>
  <div class="abs legal">© 2015 Company Name &nbsp;All right reserved &nbsp;Term of Use</div>
  <div class="abs social">
    <a aria-label="Social profile one"><i></i></a>
    <a aria-label="Social profile two"><i></i></a>
    <a aria-label="Social profile three"><i></i></a>
  </div>
</footer>

</body>
</html>
```